VFX Company Business Card Design Project

The Kestrel Works is a decentralized Visual Effects Studio servicing the television and feature film industries.
Project Brief:
Take our logo that was previously designed on Pencil Harbor and make a double sided business card.
Requirements:
- Card MUST be double sided.
- Front of card MUST have the yellow part of our logo against the dark grey background.
- Back of card is completely up to the designer.
- Back of card must include the complete company logo.
Please follow these File Preparation guidelines:
http://printnook.ca/infopage?file=filetype_en&s=PrintNook_new&lang=en
Business

```html
<!DOCTYPE html>
<html lang="en">
<head>
<meta charset="utf-8">
<title>The Kestrel Works – Business Card</title>
<link rel="stylesheet" href="https://fonts.googleapis.com/css2?family=Questrial&family=Open+Sans:wght@400&display=swap">
<style>
  :root {
    --backdrop: #c99c74;
    --card: #2b2b2b;
    --yellow: #fcc62b;
    --slate: #65717a;
    --ink: #262626;
    --paper: #f2f2f2;
    --label: #1e1e1e;
  }
  * { margin: 0; padding: 0; box-sizing: border-box; }
  html, body { width: 1200px; height: 788px; overflow: hidden; }
  body {
    background: var(--backdrop);
    position: relative;
    font-family: "Questrial", "Century Gothic", sans-serif;
  }
  .side-label {
    position: absolute;
    font-family: "Open Sans", Arial, sans-serif;
    font-size: 21px;
    color: var(--label);
    transform: translateX(-50%);
    white-space: nowrap;
  }
  .card {
    position: absolute;
    width: 525px;
    height: 300px;
    background: var(--card);
    border-radius: 22px;
    overflow: hidden;
    color: var(--paper);
  }
  .card--back { left: 338px; top: 74px; }
  .card--front-one { left: 54px; top: 446px; }
  .card--front-two { left: 622px; top: 446px; }

  .brand {
    position: absolute;
    display: flex;
    align-items: center;
    color: var(--yellow);
    white-space: nowrap;
  }
  .brand__dot {
    border-radius: 50%;
    background: var(--yellow);
    flex: none;
  }
  .brand--back { left: 28px; top: 42px; font-size: 30px; gap: 12px; }
  .brand--back .brand__dot { width: 30px; height: 30px; }
  .brand--large {
    left: 0; right: 0; top: 110px;
    justify-content: center;
    font-size: 46px;
    gap: 16px;
  }
  .brand--large .brand__dot { width: 44px; height: 44px; }
  .brand--medium {
    left: 0; right: 0; top: 130px;
    justify-content: center;
    font-size: 38px;
    gap: 14px;
  }
  .brand--medium .brand__dot { width: 36px; height: 36px; }

  .name-tag {
    position: absolute;
    left: 354px; top: 136px;
    width: 143px; height: 50px;
    background: var(--yellow);
    color: var(--ink);
    padding: 4px 0 0 10px;
  }
  .name-tag__name { font-size: 19px; line-height: 22px; letter-spacing: 0.5px; }
  .name-tag__role { font-size: 13px; line-height: 18px; letter-spacing: 0.8px; }
  .name-tag__edge {
    position: absolute;
    left: 497px; top: 136px;
    width: 28px; height: 50px;
    background: var(--slate);
  }

  .contact-list {
    position: absolute;
    left: 362px; top: 209px;
    list-style: none;
    font-size: 13px;
    line-height: 20px;
  }
  .contact-list li { display: flex; align-items: center; gap: 4px; }
  .contact-list svg { width: 11px; height: 11px; fill: var(--yellow); flex: none; }

  .address {
    position: absolute;
    left: 28px; top: 250px;
    font-size: 13px;
    line-height: 18px;
  }

  .web-line {
    position: absolute;
    left: 0; right: 0; top: 256px;
    text-align: center;
    font-size: 20px;
    letter-spacing: 3.5px;
    color: var(--paper);
  }
</style>
</head>
<body>
  <div class="side-label" style="left:600px; top:32px;">Back</div>
  <div class="side-label" style="left:327px; top:403px;">Front - 1</div>
  <div class="side-label" style="left:900px; top:403px;">Front - 2</div>

  <section class="card card--back">
    <div class="brand brand--back"><span class="brand__dot"></span>The Kestrel Works</div>

    <div class="name-tag">
      <div class="name-tag__name">Your Name</div>
      <div class="name-tag__role">Designation</div>
    </div>
    <div class="name-tag__edge"></div>

    <ul class="contact-list">
      <li><svg viewBox="0 0 12 12"><path d="M2.5 1 L4.5 1 L5 3.5 L3.8 4.5 C4.5 6 6 7.5 7.5 8.2 L8.5 7 L11 7.5 L11 9.5 C11 10.5 10 11 9 11 C4.5 10.5 1.5 7.5 1 3 C1 2 1.5 1 2.5 1 Z"/></svg>123-456-7890</li>
      <li><svg viewBox="0 0 12 12"><path d="M3.5 0.5 H8.5 A1 1 0 0 1 9.5 1.5 V10.5 A1 1 0 0 1 8.5 11.5 H3.5 A1 1 0 0 1 2.5 10.5 V1.5 A1 1 0 0 1 3.5 0.5 Z M4 2 V8.5 H8 V2 Z"/></svg>123-456-7890</li>
      <li><svg viewBox="0 0 12 12"><path d="M0.5 2.5 H11.5 V9.5 H0.5 Z M1.5 3.5 L6 6.8 L10.5 3.5 Z" fill-rule="evenodd"/></svg>info@website.com</li>
      <li><svg viewBox="0 0 12 12"><circle cx="6" cy="6" r="5.5"/></svg>www.website.com</li>
    </ul>

    <div class="address">0000#, Area Name, Street Name<br>State Name, Country code.</div>
  </section>

  <section class="card card--front-one">
    <div class="brand brand--large"><span class="brand__dot"></span>The Kestrel Works</div>
    <div class="web-line">www.website.com</div>
  </section>

  <section class="card card--front-two">
    <div class="brand brand--medium"><span class="brand__dot"></span>The Kestrel Works</div>
    <div class="web-line">www.website.com</div>
  </section>
</body>
</html>
```